Dalvick's Business Card

I need some designs for a new business card including the new logo attached. An old example of our business card is also attached to show all the data that should be included on the new design.
**I added some more examples someone had mocked up**

Contact Information for Business Card

Should include all info on other examples uploaded.

```html
<!DOCTYPE html>
<html lang="en">
<head>
<meta charset="utf-8">
<title>Dalvick's Business Card</title>
<link href="https://fonts.googleapis.com/css2?family=Montserrat:wght@500;700;800&family=Poppins:wght@600&display=swap" rel="stylesheet">
<style>
  :root{
    --blue:#0a6fbd;
    --red:#e81c24;
    --white:#ffffff;
    --stage:#c4c4c4;
  }
  *{box-sizing:border-box;margin:0;padding:0}
  html,body{width:1200px;height:800px;overflow:hidden}
  body{
    background:var(--stage);
    font-family:'Montserrat',sans-serif;
    display:flex;align-items:center;justify-content:center;gap:40px;
  }
  .card{
    position:relative;width:560px;height:320px;
    background:var(--white);border:2px solid var(--red);border-radius:18px;
    overflow:hidden;box-shadow:0 10px 24px rgba(0,0,0,.25);
  }
  /* front */
  .front .accent-block{position:absolute;top:0;left:372px;width:130px;height:58px;background:var(--red)}
  .front .brand{position:absolute;left:26px;top:26px}
  .brand-name{font-weight:800;color:var(--blue);font-size:46px;line-height:1;letter-spacing:.5px}
  .brand-tagline{font-weight:700;color:var(--red);font-size:9.5px;letter-spacing:.6px;margin-top:3px}
  .front .person{position:absolute;left:40px;top:108px;font-weight:800;color:var(--blue);font-size:22px;letter-spacing:.5px}
  .front .contact-band{
    position:absolute;left:0;top:140px;width:372px;height:70px;background:var(--blue);
    color:var(--white);padding:9px 0 0 40px;font-weight:500;font-size:17px;line-height:26px;
  }
  .contact-line{display:flex;align-items:center;gap:10px}
  .contact-line svg{width:18px;height:18px;flex:none}
  .front .credentials{position:absolute;left:40px;top:228px;color:var(--red);font-weight:800;font-size:19px;line-height:30px;letter-spacing:.3px}
  .front .mark{
    position:absolute;left:340px;top:48px;width:180px;height:180px;border-radius:50%;
    background:var(--white);border:5px solid var(--blue);
    display:flex;align-items:center;justify-content:center;
    font-weight:800;color:var(--blue);font-size:30px;
  }
  /* back */
  .back .area-band{
    position:absolute;top:0;left:0;right:0;height:56px;background:var(--red);
    color:var(--white);font-family:'Poppins',sans-serif;font-weight:600;font-size:22px;
    display:flex;align-items:center;justify-content:center;letter-spacing:.5px;
  }
  .back .brand{position:absolute;left:0;right:0;top:110px;display:flex;align-items:center;justify-content:center;gap:14px}
  .back .brand-dot{width:46px;height:46px;border-radius:50%;background:var(--red)}
  .back .brand-name{font-size:54px}
  .back .brand-tagline{font-size:11px}
  .back .cta-band{
    position:absolute;left:0;right:0;bottom:0;height:84px;background:var(--blue);
    color:var(--white);font-weight:800;font-size:19px;line-height:26px;letter-spacing:.4px;
    display:flex;flex-direction:column;align-items:center;justify-content:center;text-align:center;
  }
</style>
</head>
<body>
  <section class="card front">
    <div class="accent-block"></div>
    <div class="mark">Dalvick's</div>
    <div class="brand">
      <div class="brand-name">DALVICK'S</div>
      <div class="brand-tagline">AIR CONDITIONING &amp; HEATING SERVICE</div>
    </div>
    <div class="person">GLEN DALVICK</div>
    <div class="contact-band">
      <div class="contact-line">
        <svg viewBox="0 0 24 24" aria-hidden="true"><path fill="#fff" d="M6.6 10.8a15 15 0 0 0 6.6 6.6l2.2-2.2a1 1 0 0 1 1-.25 11.4 11.4 0 0 0 3.6.57 1 1 0 0 1 1 1V20a1 1 0 0 1-1 1A17 17 0 0 1 3 4a1 1 0 0 1 1-1h3.5a1 1 0 0 1 1 1c0 1.25.2 2.45.57 3.57a1 1 0 0 1-.25 1z"/></svg>
        <span>555.014.2290</span>
      </div>
      <div class="contact-line">
        <svg viewBox="0 0 24 24" aria-hidden="true"><rect x="2" y="5" width="20" height="14" rx="1" fill="#fff"/><path d="M2 6l10 7 10-7" fill="none" stroke="#0a6fbd" stroke-width="2"/></svg>
        <span>hvacdalvick@mailbox.com</span>
      </div>
    </div>
    <div class="credentials">
      <div>LICENSED &amp; INSURED</div>
      <div>FAMILY OWNED &amp; OPERATED</div>
    </div>
  </section>

  <section class="card back">
    <div class="area-band">Brookvale, IA &amp; Surrounding Areas</div>
    <div class="brand">
      <div class="brand-dot"></div>
      <div>
        <div class="brand-name">DALVICK'S</div>
        <div class="brand-tagline">AIR CONDITIONING &amp; HEATING SERVICE</div>
      </div>
    </div>
    <div class="cta-band">
      <div>CALL TODAY FOR ALL YOUR HVAC, REFRIGERATION &amp;</div>
      <div>PLUMBING NEEDS</div>
    </div>
  </section>
</body>
</html>
```